business card deign

Logo needs the following on it.
1. attached logo
2. Tagline - "If it keeps a drink cold or the party going...we do it!"
3. Name- Dalton Pikes, Founder and CPO
4. Address - 412 E. Carver Avenue, Ste 2207, Tampa, FL. 33917
5. Phone - 555.318.4726

```html
<!DOCTYPE html>
<html lang="en">
<head>
<meta charset="utf-8">
<title>Tundrix Business Card</title>
<link href="https://fonts.googleapis.com/css2?family=Roboto:wght@400;500;700;900&display=swap" rel="stylesheet">
<style>
  :root {
    --stage: #232323;
    --card-dark: #0e0e0e;
    --card-light: #ffffff;
    --ink: #111111;
    --ink-soft: #2a2a2a;
    --silver: #d9d9d9;
    --emboss: #f1f1f1;
  }
  * { margin: 0; padding: 0; box-sizing: border-box; }
  html, body { width: 1200px; height: 711px; overflow: hidden; }
  body {
    background: var(--stage);
    font-family: 'Roboto', sans-serif;
    display: flex;
    align-items: center;
    justify-content: center;
    gap: 48px;
  }
  .card {
    width: 540px;
    height: 320px;
    border-radius: 22px;
    position: relative;
    overflow: hidden;
    box-shadow: 0 14px 30px rgba(0,0,0,0.55);
  }

  /* Back side */
  .card-back { background: var(--card-dark); }
  .back-pattern {
    position: absolute; inset: 0;
    background: linear-gradient(135deg, #111 0%, #161616 45%, #3a3a3a 80%, #6a6a6a 100%);
    opacity: 0.9;
  }
  .back-brand {
    position: absolute; right: 46px; bottom: 96px;
    display: flex; align-items: center; gap: 6px;
  }
  .back-brand .brand-dot { width: 10px; height: 10px; border-radius: 50%; background: var(--silver); }
  .back-brand .brand-name {
    color: var(--silver); font-weight: 700; font-size: 11px; letter-spacing: 3px;
  }

  /* Front side */
  .card-front { background: var(--card-light); color: var(--ink); }
  .front-emboss {
    position: absolute; right: 0; top: 70px; width: 210px; height: 250px;
    background: radial-gradient(ellipse at 60% 55%, var(--emboss) 0%, #fafafa 55%, #ffffff 80%);
  }
  .front-tab {
    position: absolute; right: 0; top: 18px; width: 18px; height: 36px; background: var(--ink);
  }
  .holder {
    position: absolute; right: 30px; top: 18px; text-align: right;
  }
  .holder-name { font-weight: 900; font-size: 28px; line-height: 1.1; }
  .holder-role { font-weight: 400; font-size: 14px; margin-top: 2px; }

  .brand {
    position: absolute; left: 36px; top: 110px;
    display: flex; align-items: center; gap: 12px;
  }
  .brand-mark { width: 26px; height: 26px; border-radius: 50%; background: var(--ink); }
  .brand-name { font-weight: 700; font-size: 34px; letter-spacing: 12px; color: var(--ink); }

  .tagline {
    position: absolute; left: 36px; top: 186px;
    font-size: 13.5px; font-weight: 500; line-height: 1.35; color: var(--ink-soft);
  }
  .contact {
    position: absolute; left: 44px; top: 236px; list-style: none;
    font-size: 13.5px; line-height: 1.35; color: var(--ink-soft);
  }
  .contact li { display: flex; align-items: flex-start; gap: 10px; margin-bottom: 3px; }
  .contact svg { width: 14px; height: 14px; margin-top: 2px; flex: none; }
</style>
</head>
<body>
  <section class="card card-back" aria-label="Card back">
    <div class="back-pattern" role="img" aria-label="Repeating tonal brand-mark pattern on black"></div>
    <div class="back-brand">
      <span class="brand-dot"></span>
      <span class="brand-name">TUNDRIX</span>
    </div>
  </section>

  <section class="card card-front" aria-label="Card front">
    <div class="front-emboss" role="img" aria-label="Faint embossed brand-mark decoration"></div>
    <div class="front-tab"></div>
    <div class="holder">
      <p class="holder-name">Dalton Pikes</p>
      <p class="holder-role">Founder and CPO</p>
    </div>

    <div class="brand">
      <span class="brand-mark"></span>
      <span class="brand-name">TUNDRIX</span>
    </div>

    <p class="tagline">If it keeps a drink cold or<br>the party going...we do it!</p>

    <ul class="contact">
      <li>
        <svg viewBox="0 0 24 24" fill="none" stroke="#111" stroke-width="2" stroke-linecap="round" stroke-linejoin="round"><path d="M22 16.9v3a2 2 0 0 1-2.2 2 19.8 19.8 0 0 1-8.6-3.1 19.5 19.5 0 0 1-6-6A19.8 19.8 0 0 1 2.1 4.2 2 2 0 0 1 4.1 2h3a2 2 0 0 1 2 1.7c.1.9.4 1.8.7 2.7a2 2 0 0 1-.5 2.1L8 9.8a16 16 0 0 0 6 6l1.3-1.3a2 2 0 0 1 2.1-.4c.9.3 1.8.6 2.7.7a2 2 0 0 1 1.7 2z"/></svg>
        <span>555.318.4726</span>
      </li>
      <li>
        <svg viewBox="0 0 24 24" fill="none" stroke="#111" stroke-width="2" stroke-linecap="round" stroke-linejoin="round"><path d="M12 21s-7-6.2-7-11.5a7 7 0 0 1 14 0C19 14.8 12 21 12 21z"/><circle cx="12" cy="9.5" r="2.5"/></svg>
        <span>412 E. Carver Avenue,<br>Ste 2207, Tampa, FL. 33917</span>
      </li>
    </ul>
  </section>
</body>
</html>
```